Plumbing & Heating company

A leaflet containing -

Company name - Larkfield Plumbing Solutions
logo
Mobile number - 07700 914062
Landline - 01632 870215
Email - Info@larkfieldplumbing.example
website - Larkfield-plumbing.example
Social media logos - insta, Facebook

services we offer

- Boiler replacements (free quote)
- General plumbing & heating
- Tap replacements
- 1st & 2nd
- New builds & Extensions
- Cylinder replcemets

```html
<!DOCTYPE html>
<html lang="en">
<head>
<meta charset="utf-8">
<title>Larkfield Plumbing Solutions – Leaflet</title>
<link href="https://fonts.googleapis.com/css2?family=Montserrat:wght@800;900&family=Poppins:wght@400;500;600;700&display=swap" rel="stylesheet">
<style>
  :root {
    --blue-dark: #1d4f98;
    --blue: #2a76c2;
    --orange: #f47a2b;
    --orange-deep: #ee6a1c;
    --ink: #1c2230;
    --black: #17181b;
    --white: #ffffff;
    --page: #e8e8e8;
  }
  * { margin: 0; padding: 0; box-sizing: border-box; }
  html, body { width: 1200px; height: 2582px; overflow: hidden; background: var(--page); }
  .leaflet {
    position: absolute; left: 50px; top: 580px;
    width: 1031px; height: 1332px;
    background: var(--white);
    transform: scale(1.0669); transform-origin: 0 0;
    overflow: hidden;
    font-family: "Poppins", sans-serif;
    box-shadow: 0 6px 18px rgba(0,0,0,.25);
  }
  .shapes { position: absolute; inset: 0; width: 1031px; height: 1332px; }
  .abs { position: absolute; }

  .brand { left: 32px; top: 48px; color: var(--blue-dark); font-family: "Montserrat", sans-serif; font-weight: 900; }
  .brand-name { font-size: 58px; line-height: 1; letter-spacing: 1px; }
  .brand-tag { font-size: 23px; line-height: 1; letter-spacing: 2.6px; margin-top: 8px; }
  .social { top: 140px; width: 46px; height: 46px; border-radius: 50%; background: var(--orange); }
  .social.one { left: 385px; }
  .social.two { left: 437px; }

  .headline {
    left: 32px; top: 218px; color: var(--white);
    font-family: "Montserrat", sans-serif; font-weight: 900;
    font-size: 60px; line-height: 64px;
  }
  .section-title {
    left: 32px; top: 448px; color: var(--white);
    font-family: "Montserrat", sans-serif; font-weight: 900; font-size: 42px; line-height: 56px;
  }

  .services { left: 30px; top: 527px; list-style: none; }
  .service { display: flex; align-items: center; height: 68px; font-size: 29px; color: var(--ink); white-space: nowrap; }
  .service b { font-weight: 700; margin-right: 8px; }
  .service-icon { width: 62px; height: 62px; margin-right: 10px; flex: none; }

  .about {
    left: 0; top: 965px; width: 1031px; height: 223px;
    background: var(--orange); color: var(--white);
    text-align: center; font-size: 21px; line-height: 26px;
    padding: 24px 30px 0;
  }
  .about p + p { margin-top: 24px; }

  .call-more {
    left: 32px; top: 1200px; font-size: 20px; font-weight: 700; color: var(--ink);
    display: flex; align-items: center; gap: 6px; font-family: "Montserrat", sans-serif; white-space: nowrap;
  }
  .call-more .landline { font-weight: 800; }
  .mobile {
    left: 30px; top: 1250px; color: var(--white); display: flex; align-items: center; gap: 10px;
    font-family: "Montserrat", sans-serif; font-weight: 900; font-size: 58px; line-height: 78px; letter-spacing: 1px;
    white-space: nowrap;
  }
  .contact-row { display: flex; align-items: center; gap: 10px; color: var(--white); font-size: 18px; white-space: nowrap; }
  .contact-row.email { left: 632px; top: 1214px; }
  .contact-row.web { left: 610px; top: 1266px; }
  .contact-row strong { color: var(--orange); font-weight: 600; }
  .contact-icon { width: 36px; height: 36px; flex: none; }
</style>
</head>
<body>
<main class="leaflet">
  <svg class="shapes" viewBox="0 0 1031 1332">
    <defs>
      <linearGradient id="band-blue" x1="0" y1="0" x2="1" y2="0">
        <stop offset="0" stop-color="#1d4f98"/><stop offset="1" stop-color="#2f82cc"/>
      </linearGradient>
      <linearGradient id="band-orange" x1="0" y1="0" x2="1" y2="0">
        <stop offset="0" stop-color="#ee6a1c"/><stop offset="1" stop-color="#f7893a"/>
      </linearGradient>
      <linearGradient id="tone-pipes" x1="0" y1="0" x2="1" y2="1">
        <stop offset="0" stop-color="#c9c2b4"/><stop offset=".5" stop-color="#9b7a5e"/><stop offset="1" stop-color="#7a6c60"/>
      </linearGradient>
      <linearGradient id="tone-boiler" x1="0" y1="0" x2="0" y2="1">
        <stop offset="0" stop-color="#c2a585"/><stop offset=".35" stop-color="#ad8862"/><stop offset="1" stop-color="#80603f"/>
      </linearGradient>
    </defs>
    <g role="img" aria-label="Photo: new copper heating pipework laid between floor joists">
      <polygon points="567,0 842,0 640,508 365,508" fill="url(#tone-pipes)"/>
    </g>
    <g role="img" aria-label="Photo: wall-mounted white boiler with copper pipework on a plywood wall">
      <polygon points="852,0 1031,0 1031,957 470,957" fill="url(#tone-boiler)"/>
    </g>
    <polygon points="0,200 482,200 420,435 0,435" fill="url(#band-blue)"/>
    <polygon points="0,440 388,440 368,508 0,508" fill="url(#band-orange)"/>
    <polygon points="0,1245 585,1245 553,1332 0,1332" fill="url(#band-blue)"/>
    <polygon points="612,1188 1031,1188 1031,1332 560,1332" fill="var(--black)"/>
  </svg>

  <div class="abs brand">
    <div class="brand-name">LARKFIELD</div>
    <div class="brand-tag">PLUMBING SOLUTIONS</div>
  </div>
  <span class="abs social one" aria-label="Facebook"></span>
  <span class="abs social two" aria-label="Instagram"></span>

  <h1 class="abs headline">WELCOME TO<br>LARKFIELD<br>PLUMBING</h1>
  <h2 class="abs section-title">OUR SERVICES</h2>

  <ul class="abs services">
    <li class="service"><svg class="service-icon" viewBox="0 0 62 62"><circle cx="31" cy="31" r="30" fill="var(--blue)"/><circle cx="31" cy="31" r="24" fill="none" stroke="#fff" stroke-width="2"/><rect x="23" y="17" width="16" height="26" rx="3" fill="none" stroke="#fff" stroke-width="2.5"/><circle cx="31" cy="25" r="3.5" fill="#fff"/></svg><span><b>Boiler</b>Replacements (free quote)</span></li>
    <li class="service"><svg class="service-icon" viewBox="0 0 62 62"><circle cx="31" cy="31" r="30" fill="var(--blue)"/><circle cx="31" cy="31" r="24" fill="none" stroke="#fff" stroke-width="2"/><path d="M20 42 L36 26 M34 20 a7 7 0 1 0 8 8" fill="none" stroke="#fff" stroke-width="4" stroke-linecap="round"/></svg><span><b>General</b>Plumbing And Heating</span></li>
    <li class="service"><svg class="service-icon" viewBox="0 0 62 62"><circle cx="31" cy="31" r="30" fill="var(--blue)"/><circle cx="31" cy="31" r="24" fill="none" stroke="#fff" stroke-width="2"/><path d="M18 44 V30 L31 19 L44 30 V44 Z" fill="none" stroke="#fff" stroke-width="3" stroke-linejoin="round"/></svg><span><b>New Builds</b>And Extensions</span></li>
    <li class="service"><svg class="service-icon" viewBox="0 0 62 62"><circle cx="31" cy="31" r="30" fill="var(--blue)"/><circle cx="31" cy="31" r="24" fill="none" stroke="#fff" stroke-width="2"/><rect x="23" y="19" width="16" height="25" rx="7" fill="#fff"/><rect x="28" y="15" width="6" height="5" fill="#fff"/></svg><span><b>Cylinder</b>Replcemets</span></li>
    <li class="service"><svg class="service-icon" viewBox="0 0 62 62"><circle cx="31" cy="31" r="30" fill="var(--blue)"/><circle cx="31" cy="31" r="24" fill="none" stroke="#fff" stroke-width="2"/><path d="M17 26 H37 a6 6 0 0 1 6 6 V36 M27 20 V26 M22 20 H32" fill="none" stroke="#fff" stroke-width="4" stroke-linecap="round"/><circle cx="43" cy="43" r="2.5" fill="#fff"/></svg><span><b>Tap</b>Replacements</span></li>
    <li class="service"><svg class="service-icon" viewBox="0 0 62 62"><circle cx="31" cy="31" r="30" fill="var(--blue)"/><circle cx="31" cy="31" r="24" fill="none" stroke="#fff" stroke-width="2"/><path d="M20 20 L42 42 M42 20 L20 42" stroke="#fff" stroke-width="4" stroke-linecap="round"/></svg><span><b>Fix</b>1st and 2nd</span></li>
  </ul>

  <section class="abs about">
    <p>Larkfield Plumbing Solutions are a young and ambitious Plumbing &amp; Heating company with close to a decade of experience.&nbsp; We are specialists in System design &amp; installation – 1st &amp; 2nd fix, and have a considerable experience in both new build and refurbishment projects including domestic, commercial and listed properties.</p>
    <p>We offer a wide range of services covering Winchester and the surrounding areas. We are Gas safe and fully ensured.</p>
  </section>

  <div class="abs call-more">
    <span>CALL NOW FOR KNOW MORE</span>
    <svg width="24" height="24" viewBox="0 0 24 24"><circle cx="12" cy="12" r="10.5" fill="none" stroke="var(--orange)" stroke-width="2"/><path d="M8 7 l2 0 1 3 -1.5 1 a7 7 0 0 0 3.5 3.5 l1 -1.5 3 1 0 2 a1.5 1.5 0 0 1 -1.5 1.5 A9 9 0 0 1 6.5 8.5 A1.5 1.5 0 0 1 8 7 Z" fill="var(--orange)"/></svg>
    <span class="landline">01632 870215</span>
  </div>

  <div class="abs mobile">
    <svg width="44" height="58" viewBox="0 0 44 58"><rect x="8" y="2" width="26" height="46" rx="5" fill="none" stroke="#fff" stroke-width="5"/><rect x="16" y="40" width="10" height="4" rx="2" fill="#fff"/></svg>
    <span>07700 914062</span>
  </div>

  <div class="abs contact-row email">
    <svg class="contact-icon" viewBox="0 0 38 38"><circle cx="19" cy="19" r="19" fill="var(--orange)"/><rect x="9" y="12" width="20" height="14" rx="2" fill="none" stroke="#fff" stroke-width="2"/><path d="M9.5 13 L19 20 L28.5 13" fill="none" stroke="#fff" stroke-width="2"/></svg>
    <span>info@<strong>larkfieldplumbing</strong>.example</span>
  </div>
  <div class="abs contact-row web">
    <svg class="contact-icon" viewBox="0 0 38 38"><circle cx="19" cy="19" r="19" fill="var(--orange)"/><circle cx="19" cy="19" r="10" fill="none" stroke="#fff" stroke-width="2"/><ellipse cx="19" cy="19" rx="4.5" ry="10" fill="none" stroke="#fff" stroke-width="2"/><path d="M9 19 H29" stroke="#fff" stroke-width="2"/></svg>
    <span>www.<strong>larkfield-plumbing</strong>.example</span>
  </div>
</main>
</body>
</html>
```